Looking to Redesign Brevonix.com website

You guys did one of the brochures for brevonix.com and I would like to see if we can go ahead and get an estimate for a redesigned web site for the company. We currently have a couple of pages on brevonix.com which are very much a starter type site.

The new design will need to reflect some of the things discussed in the brochure. It will have flash. Needs to be designed for simple hosting using cpanels.

The site needs to have between 12 and 15 pages with flash pages to move through features. Integrated with twitter like it is now, and contact forms delivered from our CRM along with other interactive features such as subscription to newsletter, etc...

I don't have lots of details on how to proceed yet, but here are some competitor sites:

Can we take a look at potential costs involved in the redo of the site as vague as my description above can permit.

Target Market(s)

Business to Business

Number of Pages Required

5+ page

Font styles to use
Sans Serif

Requirements
Must have
• Must have professional feel. Similar to brochure. and logo.
• Include our story in the discussion.
• embedded links to our CRM for popup contact forms.
• Logo files and 2 types of brochures uploaded.
• Important to keep color scheme
Nice to have
• Flash and some movement
Should not have
• Not sure yet

```html
<!DOCTYPE html>
<html lang="en">
<head>
<meta charset="utf-8">
<title>Brevonix — Integrated Communication</title>
<link href="https://fonts.googleapis.com/css2?family=Play:wght@400;700&family=Arimo:wght@400;700&family=Open+Sans:wght@400;600&display=swap" rel="stylesheet">
<style>
:root{
  --red:#b01a1f;
  --red-dark:#7d0d12;
  --ink:#111111;
  --text:#333333;
  --muted:#666666;
  --paper:#ffffff;
  --hero-a:#0f3d66;
  --hero-b:#071624;
}
*{margin:0;padding:0;box-sizing:border-box}
html,body{width:746px;height:1200px;overflow:hidden}
body{background:radial-gradient(ellipse at center,#b8191f 0%,#9a1217 60%,#6e0a0e 100%);font-family:"Arimo",sans-serif;position:relative}
.page{position:absolute;left:62px;top:31px;width:623px;height:1122px;background:var(--paper);overflow:hidden}
.abs{position:absolute}

/* header */
.site-header{position:absolute;left:0;top:0;width:623px;height:73px;z-index:3}
.brand{left:8px;top:18px;display:flex;align-items:center;gap:6px}
.brand-dot{width:36px;height:36px;border-radius:50%;background:var(--red)}
.brand-name{font-family:"Play",sans-serif;font-weight:700;font-size:15px;color:var(--ink)}
.contact{top:14px;display:flex;align-items:center;gap:6px}
.contact small{display:block;font-size:5px;color:#999;text-transform:uppercase;letter-spacing:.3px}
.contact b{display:block;font-size:7.5px;color:var(--ink);font-weight:700}
.contact.phone b{font-size:9px}
.contact .sep{width:1px;height:22px;background:#ddd;margin-left:8px}
.nav{top:51px;right:9px;display:flex;gap:20px;font-size:7px;color:var(--ink);text-transform:uppercase}
.nav .active{color:var(--red)}

/* hero */
.hero{left:0;top:73px;width:623px;height:332px;background:radial-gradient(ellipse at 35% 40%,#2b84b8 0%,var(--hero-a) 40%,var(--hero-b) 80%)}
.hero-caption{right:8px;font-family:"Play",sans-serif;font-weight:700;color:#fff;background:rgba(120,10,14,.85);padding:1px 8px;font-size:13px;line-height:17px}
.arrow{top:261px;width:20px;height:20px;border-radius:50%;background:rgba(255,255,255,.18)}
.wave{left:0;top:355px}

/* services */
.service{text-align:center;width:90px}
.service .disc{width:50px;height:50px;border-radius:50%;background:var(--ink);border:3px solid #fff;box-shadow:0 0 0 1px #ddd;margin:0 auto;display:flex;align-items:center;justify-content:center}
.service span{display:block;margin-top:8px;font-family:"Play",sans-serif;font-weight:700;font-size:10px;color:#444;letter-spacing:.4px;line-height:12px}

/* about */
.about-photo{left:9px;top:543px;width:189px;height:150px;background:linear-gradient(135deg,#2a3440,#8fa3b5);border:2px solid #ddd}
.section-title{font-family:"Play",sans-serif;font-weight:700;color:var(--ink);font-size:15px}
.about-copy{left:225px;top:569px;width:392px;font-size:8.2px;line-height:12.8px;color:var(--text)}
.btn{background:var(--red);color:#fff;font-size:7.5px;display:flex;align-items:center;justify-content:center}
.rule{left:9px;top:722px;width:605px;border-top:1px dotted #bbb}

/* benefits */
.benefits-sub{left:0;width:623px;top:771px;text-align:center;font-family:"Open Sans",sans-serif;font-size:9.5px;color:#444}
.benefit{width:140px;text-align:center}
.benefit .disc{width:77px;height:77px;border-radius:50%;margin:0 auto;border:4px solid #fff;box-shadow:0 0 0 2px #eee;display:flex;align-items:center;justify-content:center}
.benefit p{margin-top:10px;font-size:8.5px;line-height:13.5px;color:#555}
.benefit b{color:var(--ink)}
.dots{left:295px;top:942px;display:flex;gap:4px}
.dots i{width:4px;height:4px;border-radius:50%;background:#ddd}
.dots i:first-child{background:var(--red)}

/* footer */
.footer{left:0;top:950px}
.news-title{left:10px;top:1021px;font-family:"Play",sans-serif;font-weight:700;color:#fff;font-size:13px}
.news-text{left:10px;top:1042px;font-size:6.8px;color:#ddd}
.news-input{left:10px;top:1067px;width:191px;height:25px;background:#222;border:1px solid #333;color:#999;font-size:6px;font-weight:700;padding-left:9px;display:flex;align-items:center}
.news-btn{left:202px;top:1067px;width:112px;height:25px;font-weight:700;font-size:8px;letter-spacing:.5px}
.social{left:521px;top:1062px;display:flex;gap:5px}
.social i{width:19px;height:19px;border-radius:50%;background:#333;border:1px solid #555}
.copyright{right:13px;top:1088px;font-size:7.5px;color:#ddd}
</style>
</head>
<body>
<div class="page">

  <section class="abs hero" role="img" aria-label="Businessman in a suit presenting a glowing blue network of connected people"></section>
  <div class="abs arrow" style="left:8px"></div>
  <div class="abs arrow" style="right:22px"></div>
  <div class="abs hero-caption" style="top:323px">Integrated phone services for one desk</div>
  <div class="abs hero-caption" style="top:345px">to 100 and beyond</div>

  <header class="site-header">
    <div class="abs brand"><div class="brand-dot"></div><span class="brand-name">Brevonix</span></div>
    <div class="abs contact" style="left:259px">
      <svg width="18" height="18" viewBox="0 0 18 18"><circle cx="9" cy="6" r="4" fill="#222"/><path d="M2 18c0-5 3-7 7-7s7 2 7 7z" fill="#222"/></svg>
      <div><small>Support</small><b>CHAT WITH US</b></div>
    </div>
    <div class="abs contact" style="left:371px">
      <svg width="16" height="12" viewBox="0 0 16 12"><rect x="1" y="1" width="14" height="10" fill="none" stroke="#222" stroke-width="1.4"/><path d="M1 1l7 6 7-6" fill="none" stroke="#222" stroke-width="1.4"/></svg>
      <div><small>Email us at</small><b>SALES@BREVONIX.COM</b></div>
      <div class="sep"></div>
    </div>
    <div class="abs contact phone" style="left:523px">
      <svg width="10" height="16" viewBox="0 0 10 16"><path d="M3 1l2 3-2 2c1 2 2 3 3 4l2-1 2 3-2 2C4 13 1 8 1 3z" fill="#222"/></svg>
      <div><small>Call us now</small><b>+1 555 010 4821</b></div>
    </div>
    <nav class="abs nav">
      <span class="active">Home</span><span>About</span><span>Why Brevonix</span><span>Features</span><span>Advantages</span><span>Best of Class Hardware</span>
    </nav>
  </header>

  <svg class="abs wave" width="623" height="200" viewBox="0 0 623 200">
    <defs><linearGradient id="band" x1="0" y1="0" x2="0" y2="1"><stop offset="0" stop-color="#e4e4e4"/><stop offset="1" stop-color="#ffffff"/></linearGradient></defs>
    <path d="M0 6 C150 -4 420 0 623 44 V200 H0Z" fill="var(--ink)"/>
    <path d="M0 14 C150 6 420 10 623 50 V200 H0Z" fill="var(--red)"/>
    <path d="M0 18 C150 11 420 16 623 56 V200 H0Z" fill="url(#band)"/>
    <path d="M0 190 C200 140 450 110 623 150 V200 H0Z" fill="#fff"/>
  </svg>

  <section class="services">
    <div class="abs service" style="left:13px;top:399px"><div class="disc"><svg width="14" height="14" viewBox="0 0 14 14"><circle cx="3" cy="11" r="2" fill="#fff"/><path d="M1 6a7 7 0 0 1 7 7M1 1a12 12 0 0 1 12 12" fill="none" stroke="#fff" stroke-width="2"/></svg></div><span>WIRELESS</span></div>
    <div class="abs service" style="left:119px;top:391px"><div class="disc"><svg width="14" height="11" viewBox="0 0 14 11"><rect width="14" height="11" rx="1" fill="#fff"/><path d="M0 1l7 5 7-5" fill="none" stroke="#111" stroke-width="1.3"/></svg></div><span>EMAIL</span></div>
    <div class="abs service" style="left:221px;top:407px"><div class="disc"><svg width="14" height="14" viewBox="0 0 14 14"><rect x="1" y="4" width="12" height="10" fill="#fff"/><rect x="4" y="0" width="6" height="4" fill="#fff"/><rect x="3" y="7" width="2" height="2" fill="#111"/><rect x="6" y="7" width="2" height="2" fill="#111"/><rect x="9" y="7" width="2" height="2" fill="#111"/></svg></div><span>FAX</span></div>
    <div class="abs service" style="left:327px;top:428px"><div class="disc"><svg width="15" height="13" viewBox="0 0 15 13"><path d="M2 1h11v7H6l-3 3V8H2z" fill="none" stroke="#fff" stroke-width="1.6"/></svg></div><span>TEXT<br>MESSAGING</span></div>
    <div class="abs service" style="left:423px;top:439px"><div class="disc"><svg width="14" height="14" viewBox="0 0 14 14"><circle cx="7" cy="7" r="6.5" fill="#fff"/><path d="M4 3c2 1 1 3 3 3s1 3-1 4M10 9c1-1 2 0 2 1" fill="none" stroke="#111" stroke-width="1.3"/></svg></div><span>WEB</span></div>
    <div class="abs service" style="left:530px;top:428px"><div class="disc"><svg width="8" height="13" viewBox="0 0 8 13"><rect x="0.7" y="0.7" width="6.6" height="11.6" rx="1" fill="none" stroke="#fff" stroke-width="1.4"/><circle cx="4" cy="10" r="0.9" fill="#fff"/></svg></div><span>PHONE</span></div>
  </section>

  <section class="about">
    <div class="abs about-photo" role="img" aria-label="Businessman holding miniature figures of a team on puzzle pieces"></div>
    <h2 class="abs section-title" style="left:225px;top:541px">ABOUT</h2>
    <p class="abs about-copy">Brevonix Universal Communication was born out of the desire to offer reliable, affordable phone systems for the small- to medium-sized business. Since 2003, we have offered hosted VOIP PBX and call routing services, but they were bundled with larger IT services. As such, it was only cost-effective for the large corporate client. By re-imagining Brevonix and creating a separate company, our clients benefit from those years of fine-tuning and we could serve the needs of a much broader range of businesses. Brevonix melds the fresh ideas of youth with the reliability of experience to find the truly best working communication solutions for the companies we serve.</p>
    <a class="abs btn" style="left:225px;top:670px;width:73px;height:23px">Read More</a>
  </section>

  <div class="abs rule"></div>

  <section class="benefits">
    <h2 class="abs section-title" style="left:0;width:623px;text-align:center;top:749px">BENEFITS</h2>
    <p class="abs benefits-sub">Discovering your needs, creating solutions that truly work</p>
    <div class="abs benefit" style="left:20px;top:811px"><div class="disc" style="background:var(--red)"><svg width="26" height="22" viewBox="0 0 26 22"><path d="M10 2L2 9l8 7v-4c6 0 10 1 13 8 0-8-4-13-13-13z" fill="#fff"/></svg></div><p><b>Quick ROI:</b> Equipment is in-<br>cluded in the service</p></div>
    <div class="abs benefit" style="left:170px;top:811px"><div class="disc" style="background:var(--ink)"><svg width="18" height="22" viewBox="0 0 18 22"><path d="M4 10V6a5 5 0 0 1 10 0v4" fill="none" stroke="#fff" stroke-width="2.4"/><rect x="1" y="10" width="16" height="12" rx="1" fill="#fff"/></svg></div><p><b>Secure:</b> Encrypted lines</p></div>
    <div class="abs benefit" style="left:319px;top:811px"><div class="disc" style="background:var(--red)"><svg width="24" height="18" viewBox="0 0 24 18"><path d="M2 9l7 7L22 2" fill="none" stroke="#fff" stroke-width="4"/></svg></div><p><b>Easy installation:</b> Very little<br>business interruption</p></div>
    <div class="abs benefit" style="left:468px;top:811px"><div class="disc" style="background:var(--red)"><svg width="20" height="24" viewBox="0 0 20 24"><path d="M1 2h18v9c0 6-5 10-9 12C6 21 1 17 1 11z" fill="#fff"/><path d="M10 5h5v6c0 4-3 6-5 8z" fill="var(--red)"/></svg></div><p><b>Safety:</b> 911 notification to man-<br>agers</p></div>
    <div class="abs dots"><i></i><i></i><i></i><i></i></div>
  </section>

  <svg class="abs footer" width="623" height="172" viewBox="0 0 623 172">
    <rect width="623" height="172" fill="#0b0b0b"/>
    <path d="M0 40 C150 40 420 60 520 90 C580 80 610 60 623 46 V80 C560 110 500 115 420 104 C280 80 120 65 0 62Z" fill="var(--red-dark)"/>
    <path d="M0 0 H623 V40 C590 70 540 86 480 84 C360 60 170 32 0 22Z" fill="#fff"/>
    <path d="M0 22 C170 32 360 60 480 84 C540 86 590 70 623 40 V52 C590 82 540 98 470 96 C350 72 170 46 0 38Z" fill="var(--red)"/>
  </svg>
  <h3 class="abs news-title">NewsLetter Subscription</h3>
  <p class="abs news-text">Lorem ipsum dolor sit amet, consectetur adipiscing elit.</p>
  <div class="abs news-input">Enter Your Email Id</div>
  <a class="abs btn news-btn">SUBSCRIBE NOW</a>
  <div class="abs social"><i></i><i></i><i></i><i></i></div>
  <p class="abs copyright">© 2016 Yoursite. All Rights Reserved.</p>

</div>
</body>
</html>
```